Site re-branding and modernization

Two Managed Service Providers (Information Technology) have merged and need an update to their website. The site needs to be re-branded from "Ridgeline Computing" with a blue theme to "Harbor Systems" with an orange theme.

Harbor Systems provides small and medium business with an outsourced IT department, offering enterprise level IT to business that otherwise wouldn't have it. Our marketing has been centered around a row of apples with one orange and a caption that says, "We do IT our own way and we're happy about it!" Hence the orange color scheme needed as well as a site that stands out from the typical MSP site.

We would like to maintain our current site in order to retain SEO, update the technology used (current site is flash based), mobile (Zelphone, Zelpad, Orbitel Phone) compatible and Color Theme update (likely orange and white).

My current site:
http://www.harborsystems-example.net

My chief local competition (who we want to look better than):
http://www.quillbyte-example.com/

Other MSP sites (people we want to stand out from):
http://www.lanternops-example.com/
http://www.fernacle-example.com/
Updates

Please send your email to mpatterly@harborsys-example.com if you are interested in this project so I can send you a filecrate link to the existing site files for you to work with.

https://www.filecrate-example.com/sh/4k2pq8wzrbn51tx/QQL9MvaHsT2ZwpeuNoXKA74b

We would like to have a Call to action form on the main page and an informational Video. In addition we would like the following Categories and coorisponding Icons on the Main Page. We will also need a page for each Sub-Category. The Tag line on the Landing Page / Banner should read "Enterprise Solutions for Everyone" Managed IT >Law Firms .>Associations / Nonprofits > Financial Services > Healthcare >Education Cloud Services >Server > Desktop >Managed Wireless > Voice > Restaurant Point of Sale >Pellmark Suite 365 Migrations Data Center > Managed Servers > Managed Desktops >Disaster Recovery Hosting Professional Services >Virtualization >Backup & DR Planning >Corvane Links >Mobile or Virtual Office Solutions

Target Market(s)

Small and medium business that want to have the best possible IT support.

Industry/Entity Type

Marketing

Colors
f37022

Requirements
Must have
• Convert Site from Flash to Latest web design technology i.e. DHTML. Site must be mobile friendly. Convert all Ridgeline Computing Logo Marks to Harbor Systems Logo. Change Color Theme to match uploaded files.

```html
<!DOCTYPE html>
<html lang="en">
<head>
<meta charset="utf-8">
<title>Harbor Systems — Enterprise IT for Small &amp; Mid-Size Business</title>
<link rel="stylesheet" href="https://fonts.googleapis.com/css2?family=Alfa+Slab+One&family=Lato:wght@300;400;700&display=swap">
<style>
:root{
  --orange:#f37022;
  --black:#000;
  --white:#fff;
  --ink:#1a1a1a;
  --grey-head:#707070;
  --field:#9a9a9a;
  --footer:#3d4242;
  --footer-text:#d9dcdc;
}
*{margin:0;padding:0;box-sizing:border-box}
html,body{width:853px;height:1200px;overflow:hidden}
body{position:relative;background:var(--white);font-family:"Lato",Arial,sans-serif;color:var(--ink)}
a{color:inherit;text-decoration:none}
.abs{position:absolute}

/* utility bar */
.utility-bar{left:0;top:0;width:853px;height:25px;background:var(--black);color:var(--white);font-size:10px;font-weight:700;display:flex;justify-content:flex-end;align-items:center;padding-right:16px;gap:6px;white-space:nowrap}
.utility-bar .muted{font-weight:400;color:#ccc}

/* header */
.brand{left:30px;top:44px}
.brand-name{display:flex;align-items:center;gap:8px;font-weight:700;font-size:21px;color:var(--ink);white-space:nowrap}
.brand-mark{width:16px;height:16px;background:var(--orange)}
.brand-tagline{margin-top:28px;font-size:8px;font-weight:700;color:var(--ink);white-space:nowrap}
.social{top:46px;right:20px;display:flex;gap:12px}
.social span{width:24px;height:24px;border-radius:50%;background:var(--orange)}
.call-today{top:86px;right:30px;font-size:15px;letter-spacing:.5px;white-space:nowrap}

/* navigation */
.main-nav{left:0;top:120px;width:853px;height:52px;background:var(--orange);display:flex;align-items:stretch;padding-left:12px}
.main-nav a{display:flex;align-items:center;padding:0 12px;font-size:14px;color:var(--black);white-space:nowrap;flex-shrink:0}
.main-nav a.active{background:var(--black);color:var(--white)}

/* hero */
.hero-video{left:0;top:172px;width:426px;height:344px;background:var(--black)}
.hero-video .label{left:296px;top:12px;font-size:16px;color:var(--white);white-space:nowrap}
.hero-video .title{left:43px;top:40px;font-family:"Alfa Slab One",Georgia,serif;font-size:41px;color:var(--orange)}
.hero-video .subtitle{left:43px;top:90px;font-size:39px;font-weight:300;color:var(--orange);white-space:nowrap}
.play-button{left:188px;top:146px;width:50px;height:50px;background:#444;border-radius:3px;display:flex;align-items:center;justify-content:center}
.hero-offer{left:426px;top:172px;width:427px;height:344px;background:radial-gradient(ellipse at 75% 45%,#d9c3b3 0%,#8a7d74 25%,#3a3836 55%,#1c1c1c 100%)}
.offer-head{left:22px;top:14px;font-family:"Alfa Slab One",Georgia,serif;color:var(--white);font-size:21px;line-height:25px;white-space:nowrap}
.offer-head .small{font-size:18px}
.offer-copy{left:22px;top:190px;color:var(--white);font-size:12.5px;font-weight:700;line-height:16px;white-space:nowrap}
.offer-copy em{display:block}
.audit-form{left:22px;top:233px;width:350px}
.audit-form .field{width:256px;height:24px;background:var(--field);color:var(--white);font-size:11px;padding:5px 6px;margin-bottom:1px;display:block}
.audit-form .submit{position:absolute;left:256px;top:53px;width:94px;height:24px;background:var(--black);color:#ccc;font-size:11px;padding:5px 25px}

/* intro */
.intro-panel{left:0;top:516px;width:283px;height:341px;background:var(--orange);color:var(--white);text-align:right}
.intro-panel h1{position:absolute;right:11px;top:56px;font-family:"Alfa Slab One",Georgia,serif;font-weight:400;font-size:42px;line-height:52px}
.intro-panel .for{position:absolute;right:11px;top:172px;font-size:24px;line-height:28px;white-space:nowrap}
.benefits{top:570px}
.benefits.left{left:301px;width:240px}
.benefits.right{left:571px;width:242px}
.benefits h3{font-size:15.5px;font-weight:400;color:var(--grey-head);line-height:17px}
.benefits p{font-size:13.8px;line-height:17px;margin-bottom:15px}
.benefits.right p{margin-bottom:18px}

/* footer */
.site-footer{left:0;top:857px;width:853px;height:343px;background:var(--footer);color:var(--footer-text)}
.foot-col{top:54px;font-size:10px;line-height:12.3px;white-space:nowrap}
.foot-col h4{color:var(--white);font-size:13.5px;font-weight:700;margin-bottom:15px}
.foot-col .hl{color:var(--white)}
.foot-col .indent{padding-left:22px}
.foot-links{top:250px;left:0;width:853px;text-align:center;color:var(--white);font-size:10px}
.foot-links span{margin:0 12px}
.copyright{top:318px;left:0;width:853px;text-align:center;color:var(--white);font-size:6px}
</style>
</head>
<body>

<nav class="utility-bar abs">
  <a href="#">Home</a><span>|</span><a href="#">Submit Trouble Ticket</a><span>|</span><a class="muted" href="#">Pay Bill Online</a><span>|</span><a href="#">Blog</a><span>|</span><a href="#">Client Login</a>
</nav>

<header>
  <div class="brand abs">
    <div class="brand-name"><span class="brand-mark"></span>Harbor Systems</div>
    <div class="brand-tagline">We do IT our own way and we're happy about it!</div>
  </div>
  <div class="social abs" aria-label="Social links"><span></span><span></span><span></span></div>
  <div class="call-today abs">CALL TODAY &nbsp;&nbsp;(555) 014-2290</div>
</header>

<nav class="main-nav abs">
  <a href="#">HOME</a>
  <a class="active" href="#">EXTRAORDINARY SERVICES</a>
  <a href="#">CLOUD SERVICES</a>
  <a href="#">DATA CENTER</a>
  <a href="#">PROFESSIONAL SERVICES</a>
  <a href="#">ABOUT US</a>
</nav>

<section class="hero-video abs">
  <div class="label abs">Watch our video</div>
  <div class="title abs">Client</div>
  <div class="subtitle abs">Testimonials</div>
  <div class="play-button abs">
    <svg width="16" height="18" viewBox="0 0 16 18"><path d="M2 1 L15 9 L2 17 Z" fill="#000"/></svg>
  </div>
</section>

<section class="hero-offer abs" role="img" aria-label="Photo of a businessman extending his hand">
  <div class="offer-head abs">ARE YOU AWARE<br><span class="small">of what your business<br>is missing?</span></div>
  <div class="offer-copy abs">Get answers today with a no charge comprehensive Network Audit.<em>A $500.00 VALUE</em></div>
  <form class="audit-form abs">
    <span class="field">Name</span>
    <span class="field">Email</span>
    <span class="field">Phone</span>
    <span class="submit">SUBMIT</span>
  </form>
</section>

<section class="intro-panel abs">
  <h1>Harbor<br>Systems</h1>
  <div class="for">for<br><em>YOUR</em> business</div>
</section>

<div class="benefits left abs">
  <h3>Are your computers slow ?</h3>
  <p>Or are they making you and your employees wait ?</p>
  <h3>Do you have confidence in your network ?</h3>
  <p>Is your network improving security and collaboration or hindering it ?</p>
  <h3>Is your technology working for your business ?</h3>
  <p>Are you and your staff forced to waste time on annoying computer issues ?</p>
</div>

<div class="benefits right abs">
  <h3>Proactive Care</h3>
  <p>Dedication to the prevention of down-time, data loss and other business tech-nology disasters before they happen.</p>
  <h3>Round the Clock Maintenance</h3>
  <p style="margin-bottom:2px">24X7 access to remote and on-site server remediation services at a flat, monthly rate ?</p>
  <h3>Live Help Desk Support</h3>
  <p>Fast and reliable IT solutions provided 24x7 for your employees.</p>
</div>

<footer class="site-footer abs">
  <div class="foot-col abs" style="left:43px">
    <h4>Top Level Services</h4>
    Managed IT<br><span class="hl">Small &amp; Mid-Size Businesses</span><br>Law Firms<br>Associations / Non-Profits<br>Financial Services<br>Healthcare<br>Education
  </div>
  <div class="foot-col abs" style="left:196px">
    <h4>Cloud Services</h4>
    Backup &amp; Disaster Recovery<br>Public &amp; Private Cloud Server<br>Solutions<br>Voice<br>Pellmark Suite 365 Migrations<br>Restaurant Point of Sale
  </div>
  <div class="foot-col abs" style="left:349px">
    <h4>Data Center</h4>
    BManaged Servers<br>DR Hosting<br>Virtual Office Solutions
  </div>
  <div class="foot-col abs" style="left:503px">
    <h4>Professional Services</h4>
    Virtualization<br>Corvane Links<br>Virtual Office Design &amp;<br><span class="indent">Deployment</span><br>Restaurant POS Design &amp;<br><span class="indent">Deployment</span>
  </div>
  <div class="foot-col abs" style="left:656px">
    <h4>About Us</h4>
    Who we are<br>Testimonials<br>Partners<br>Locations<br>Site
  </div>
  <div class="foot-links abs">franchise opportunites<span>|</span>terms<span>|</span>privacy policy</div>
  <div class="copyright abs">opyright © 2014 harbor systems llc</div>
</footer>

</body>
</html>
```